Sophisticated, clean website reflecting my feminine, playful side to sell my abstract art,

I need a website no more than 3 pages to showcase my paintings, a little about me and some contact info. I do abstracts so looking for something a little edgy, yet feminine and current.
Updates

Hi there, These are some artists websites that I Iike: Marnelvoss.com (I like how airy it is) peterwallombry.com garethpolvens.com (I like how it scrolls) I'll need a place for a photo ( a headshot-i do not have it yet so I'll need to be able to upload that later) as well as an area for my bio. Also, it's important that I will be able to upload any new photos and descriptions easily so it should be user friendly. Lastly, I like in a sunny place so would like to have this seem upbeat and playful as that is how i like to paint. thanks-I'm trying to upload my photos now -

Target Market(s)

ppl ages 35-70 who want large scale art for their homes

Industry/Entity Type

art

Coding

Coded - Design and coding required

Number of Pages Required

3 page

Colors

Designer to choose colors to be used in the design.

Requirements
Must have
• photos of my art, a place for my bio, be easy to reach me. tasteful-nothing too "in your face" -my clients are pretty high end and organized. They like clean lines
Nice to have
• sophisticated background, muted tones in the back-similar clean font throughout-no cursive
Should not have
• too many dark areas. Too many blocks of color. Too serious.

```html
<!DOCTYPE html>
<html lang="en">
<head>
<meta charset="utf-8">
<title>Helena Marsh — Art</title>
<link rel="stylesheet" href="https://fonts.googleapis.com/css2?family=Inter:wght@300;400&family=Playfair+Display:ital,wght@0,400;0,700;1,400&display=swap">
<style>
  :root {
    --ink: #14131a;
    --muted: #3a3944;
    --violet: #7b2ff2;
    --white: #ffffff;
    --rule: #d9d6e2;
    --lilac: rgba(196, 176, 245, 0.55);
    --butter: rgba(255, 250, 205, 0.7);
  }
  * { margin: 0; padding: 0; box-sizing: border-box; }
  html, body { width: 1200px; height: 3104px; overflow: hidden; }
  body {
    position: relative;
    font-family: "Inter", sans-serif;
    color: var(--ink);
    background:
      radial-gradient(ellipse 420px 360px at 40px 40px, var(--lilac), transparent 70%),
      radial-gradient(ellipse 380px 400px at 1200px 420px, var(--butter), transparent 70%),
      radial-gradient(ellipse 420px 380px at 1180px 900px, var(--lilac), transparent 70%),
      radial-gradient(ellipse 460px 420px at 0 1900px, var(--lilac), transparent 70%),
      radial-gradient(ellipse 440px 400px at 1200px 2300px, var(--lilac), transparent 70%),
      radial-gradient(ellipse 460px 380px at 0 2700px, var(--butter), transparent 70%),
      radial-gradient(ellipse 440px 380px at 1200px 3000px, var(--lilac), transparent 70%),
      var(--white);
  }
  .abs { position: absolute; }
  em { font-family: "Playfair Display", serif; font-style: italic; }

  .nav-link { top: 42px; font-size: 17px; font-weight: 400; color: var(--ink); text-decoration: none; }
  .nav-contact {
    left: 990px; top: 34px; width: 97px; height: 36px;
    background: var(--violet); color: var(--white);
    font-size: 17px; display: flex; align-items: center; justify-content: center;
  }
  .site-title { left: 113px; top: 108px; font-family: "Playfair Display", serif; font-weight: 700; font-size: 44px; letter-spacing: -0.2px; }
  .accent-rule { left: 445px; top: 195px; width: 67px; height: 2px; background: var(--violet); }
  .tagline { left: 445px; top: 206px; font-size: 34px; font-weight: 300; line-height: 43px; }

  .artwork { box-shadow: 0 24px 50px rgba(120, 100, 170, 0.18); }
  .hero-art { left: 112px; top: 347px; width: 559px; height: 340px;
    background: linear-gradient(100deg, #e84a3a 0%, #3dbb9f 22%, #f2c9a2 45%, #1e5c55 65%, #f5c8a0 78%, #f3c530 100%); }

  .section-label { left: 0; width: 1200px; text-align: center; font-size: 22px; font-weight: 300; }
  .section-heading { left: 0; width: 1200px; text-align: center; font-size: 41px; font-weight: 300; line-height: 49px; }

  .work-title { font-family: "Playfair Display", serif; font-size: 26px; font-weight: 400; }
  .work-note { font-size: 13px; color: var(--muted); }

  .art-glamour { left: 122px; top: 984px; width: 382px; height: 450px;
    background: radial-gradient(circle at 55% 40%, #f08a2c 0%, #e66b3a 28%, #2f6fd8 55%, #5bc4ee 100%); }
  .art-legend { left: 613px; top: 984px; width: 463px; height: 384px;
    background: linear-gradient(90deg, #e9a6c8 0%, #5cc3df 35%, #e7c23c 60%, #9a78c9 100%); }
  .art-lincoln { left: 122px; top: 1606px; width: 465px; height: 400px;
    background: linear-gradient(160deg, #d6b48c 0%, #c49a6e 45%, #6c8a58 70%, #2c2b33 100%); }
  .art-scratch { left: 696px; top: 1571px; width: 380px; height: 446px;
    background: radial-gradient(ellipse at 50% 55%, #c9692e 0%, #a2582f 22%, #2f5a3a 48%, #2a4a33 100%); }

  .process-label { left: 122px; top: 2349px; font-size: 24px; font-weight: 300; }
  .process-heading { left: 122px; top: 2384px; font-size: 42px; font-weight: 300; line-height: 48px; }
  .process-video { left: 595px; top: 2247px; width: 492px; height: 328px;
    background: radial-gradient(ellipse at 50% 52%, #f0d3d6 0%, #ebd6dc 38%, #e3e2ee 70%, #dcdcea 100%); }
  .play-icon { left: 798px; top: 2368px; }

  .cta-button {
    left: 494px; top: 2853px; width: 211px; height: 51px;
    background: var(--violet); color: var(--white);
    font-size: 15px; letter-spacing: 0.3px;
    display: flex; align-items: center; justify-content: center;
  }
  .footer-rule { left: 113px; top: 2964px; width: 974px; height: 1px; background: var(--rule); }
  .copyright { left: 113px; top: 2997px; font-size: 15px; }
  .footer-link { top: 2998px; font-size: 13px; color: var(--ink); }
</style>
</head>
<body>
  <header>
    <nav>
      <span class="abs nav-link" style="left:677px">Gallery</span>
      <span class="abs nav-link" style="left:784px">Clients</span>
      <span class="abs nav-link" style="left:890px">About</span>
      <span class="abs nav-contact">Contact</span>
    </nav>
    <h1 class="abs site-title">Helena Marsh</h1>
    <div class="abs accent-rule"></div>
    <p class="abs tagline">I’m passionate about making art that<br>represent <em>society</em> and <em>technology</em></p>
    <div class="abs artwork hero-art" role="img" aria-label="Featured abstract painting with red, teal, peach and yellow shapes"></div>
  </header>

  <section class="recent-works">
    <p class="abs section-label" style="top:790px">Recent Works</p>
    <h2 class="abs section-heading" style="top:822px;font-weight:300">Check out some of<br>my <em>Finest</em> work</h2>

    <div class="abs artwork art-glamour" role="img" aria-label="Colourful portrait painting titled Glamourity"></div>
    <p class="abs work-title" style="left:122px;top:1460px">Glamourity</p>
    <p class="abs work-note" style="left:122px;top:1499px">A powerful story can change evrything</p>

    <div class="abs artwork art-legend" role="img" aria-label="Expressive portrait painting titled Legend of Ventura"></div>
    <p class="abs work-title" style="left:613px;top:1394px">Legend of Ventura</p>
    <p class="abs work-note" style="left:613px;top:1433px">The legends Never die</p>

    <div class="abs artwork art-lincoln" role="img" aria-label="Vintage style illustrated scene titled Oh no Lincoln"></div>
    <p class="abs work-title" style="left:122px;top:2034px">Oh no Lincoln</p>
    <p class="abs work-note" style="left:122px;top:2073px">Kids are mysterious</p>

    <div class="abs artwork art-scratch" role="img" aria-label="Torn poster collage artwork titled Scraaaatch!"></div>
    <p class="abs work-title" style="left:696px;top:2034px">Scraaaatch!</p>
    <p class="abs work-note" style="left:696px;top:2073px">We love to hide from the mess</p>
  </section>

  <section class="process">
    <p class="abs process-label">Process</p>
    <h2 class="abs process-heading">See The <em>approach</em><br>to make <em>arts</em></h2>
    <div class="abs artwork process-video" role="img" aria-label="Video still of a pink sketch sheet with pencils on a desk"></div>
    <svg class="abs play-icon" width="86" height="86" viewBox="0 0 86 86" aria-hidden="true">
      <circle cx="43" cy="43" r="42" fill="none" stroke="#ffffff" stroke-width="2"/>
      <path d="M34 29 L58 43 L34 57 Z" fill="none" stroke="#ffffff" stroke-width="2" stroke-linejoin="round"/>
    </svg>
  </section>

  <section class="contact">
    <p class="abs section-label" style="top:2682px">Contact Us</p>
    <h2 class="abs section-heading" style="top:2716px">Ready to <em>stand out</em><br>among the crowd?</h2>
    <span class="abs cta-button">LET’S WORK TOGETHER</span>
  </section>

  <footer>
    <div class="abs footer-rule"></div>
    <p class="abs copyright">Copyright © 2021 Marshstudio.com</p>
    <span class="abs footer-link" style="left:760px">Home</span>
    <span class="abs footer-link" style="left:824px">Gallery</span>
    <span class="abs footer-link" style="left:895px">Clients</span>
    <span class="abs footer-link" style="left:965px">About</span>
    <span class="abs footer-link" style="left:1030px">Contacts</span>
  </footer>
</body>
</html>
```